redesign of my existing custom website into Wordpress based website

I need someone to redesign my current website into something more classy, simplistic, modern and on trend. I would like it set up on Wordpress in a way thats easy for me to make my own additions to blogs/price changes and promotion banners. I will also need a page that is password protected so members can login and have access to all my training videos and resources.
website is www.tidewellmamas.com.au

Target Market(s)

new mums

Industry/Entity Type

Fitness

Coding

Coded - Design and coding required

Number of Pages Required

5+ page

Colors
33a6d7

Requirements
Must have
• chic, modern, stylish and simplistic.
• a call to action above the page fold
• mobile friendly conversion
• a pop up message as soon as someone enters my sight offering my free report
• a members page that is password protected containing 3 youtube videos and 6 pdf attachments as resources
• a home page
• a contact us page
• an about us page
• a blog page
• a store page
Nice to have
• some examples of my peers websites that I like:
• www.norapellwick.com
• https://www.9qlr.com
• https://41bytedgarth.com
Should not have
• anything gimmicky

```html
<!DOCTYPE html>
<html lang="en">
<head>
<meta charset="utf-8">
<title>Tidewell Mamas – Home Fitness</title>
<link href="https://fonts.googleapis.com/css2?family=Lato:wght@400;700;900&family=Courgette&display=swap" rel="stylesheet">
<style>
:root{
  --blue:#33a6d7;
  --blue-deep:#1f7fb8;
  --blue-band:#2d8fcb;
  --ink:#2b2b2b;
  --body:#555;
  --pink:#e5197e;
  --gold:#c9ad2e;
  --cyan:#1fc3ec;
  --footer:#232323;
  --white:#fff;
}
*{box-sizing:border-box;margin:0;padding:0}
html,body{width:1200px;height:3593px;overflow:hidden}
body{font-family:'Lato',sans-serif;color:var(--ink);background:var(--white);position:relative}
.abs{position:absolute}
section,header,footer{position:absolute;left:0;width:1200px}
.btn{position:absolute;background:var(--blue);color:var(--white);font-weight:700;display:flex;align-items:center;justify-content:center;border-radius:2px;font-size:15px}
p{line-height:1.6}

/* hero */
.hero{top:0;height:556px;background:linear-gradient(100deg,#f4f4f3 0%,#ecebe8 45%,#dcd8d2 70%,#cfc9c2 100%)}
.hero-photo{position:absolute;right:0;top:0;width:720px;height:556px;background:radial-gradient(ellipse at 65% 55%,#d7c7b9 0%,#e3dcd3 40%,rgba(236,235,232,0) 75%)}
.brand{position:absolute;left:96px;top:22px;display:flex;align-items:center;gap:10px}
.brand-dot{width:44px;height:44px;border-radius:50%;background:var(--blue)}
.brand-name{font-size:19px;font-weight:700;color:var(--blue);line-height:1.1}
.nav{position:absolute;top:30px;left:0;width:1200px;font-size:15px;color:var(--ink)}
.nav span{position:absolute}
.join{top:22px;left:984px;width:118px;height:36px;font-size:13px}
.hero h1{position:absolute;left:96px;top:208px;font-size:34px;font-weight:900;letter-spacing:.3px}
.hero .script{position:absolute;left:96px;top:262px;font-family:'Courgette',cursive;font-size:42px;color:var(--blue)}
.hero .sub{position:absolute;left:96px;top:335px;font-size:17px;font-weight:700}
.hero .btn{left:100px;top:383px;width:188px;height:48px;font-size:17px;font-weight:400}
.dots{position:absolute;left:100px;top:463px;display:flex;gap:6px}
.dots i{width:13px;height:13px;border-radius:50%;border:2px solid #8aa;display:block}
.dots i:first-child{background:var(--blue);border-color:var(--blue)}

/* intro */
.intro{top:556px;height:462px}
.intro h2{position:absolute;left:100px;top:50px;font-size:27px;font-weight:400;color:var(--blue)}
.intro .rule{position:absolute;left:100px;top:97px;width:270px;height:2px;background:var(--blue)}
.intro .lead{position:absolute;left:100px;top:115px;font-size:16px;font-weight:700}
.intro .copy{position:absolute;left:100px;top:152px;width:665px;font-size:13px;color:var(--body)}
.intro .copy p{margin-bottom:10px}
.intro .btn{left:100px;top:352px;width:116px;height:43px}
.optin{position:absolute;left:798px;top:62px;width:304px;height:352px;background:var(--blue);color:var(--white);text-align:center;padding:34px 26px 0;box-shadow:0 4px 12px rgba(0,0,0,.2)}
.optin h3{font-size:17px;font-weight:900;line-height:1.3}
.optin .note{font-size:12px;margin:12px 0 16px;line-height:1.5}
.optin .field{height:38px;background:var(--white);border-radius:2px;margin-bottom:11px;color:#666;font-size:12px;text-align:left;padding:12px 10px}
.optin .submit{height:44px;border:2px solid var(--white);border-radius:2px;font-weight:900;font-size:15px;display:flex;align-items:center;justify-content:center;margin-top:14px}
.badge{position:absolute;left:1054px;top:30px;width:88px;height:88px;border-radius:50%;background:var(--pink);color:var(--white);font-weight:700;font-size:15px;display:flex;align-items:center;justify-content:center;text-align:center;line-height:1.2;border:3px solid var(--white)}

/* programs band */
.band{top:1018px;height:623px;background:linear-gradient(180deg,#3aa3d9,#2a8bc7)}
.band-title{position:absolute;width:1200px;text-align:center;color:var(--white)}
.band-title .pre{font-size:19px}
.band-title .main{font-size:26px;font-weight:900;margin-top:8px}
.card{position:absolute;top:163px;width:307px;height:400px;background:var(--white);text-align:center;box-shadow:0 3px 8px rgba(0,0,0,.2)}
.card .photo{height:153px;margin:0}
.card .icon{position:absolute;left:133px;top:131px;width:42px;height:42px;border-radius:50%;background:var(--blue);border:3px solid var(--white)}
.card h4{margin:72px 20px 0;font-size:17px;line-height:1.35}
.card p{margin:10px 24px 0;font-size:13px;color:var(--body)}

/* founder */
.founder{top:1641px;height:448px}
.founder .photo{position:absolute;left:96px;top:35px;width:239px;height:396px;background:linear-gradient(180deg,#e7e3dd,#b8e36a 45%,#8ed33c 70%,#555 100%)}
.founder .label{position:absolute;left:398px;top:48px;font-size:20px;font-weight:700}
.founder .name{position:absolute;left:398px;top:84px;font-size:26px;color:var(--blue)}
.founder .copy{position:absolute;left:398px;top:130px;width:700px;font-size:13px;color:var(--body)}
.founder .copy p{margin-bottom:10px}
.founder .copy b{color:var(--pink);font-weight:400}
.founder .btn{left:398px;top:354px;width:116px;height:43px}

/* results */
.results{top:2089px;height:582px;background:linear-gradient(180deg,#2e93cd,#1f79b3)}
.result{position:absolute;top:0;width:260px;text-align:center;color:var(--white)}
.result .ring{position:absolute;top:167px;left:15px;width:230px;height:230px;border-radius:50%;border:5px solid var(--white);display:flex;align-items:center;justify-content:center}
.result .shot{width:110px;height:150px;background:linear-gradient(180deg,#efe6dc,#c9b5a1)}
.result .who{position:absolute;top:425px;width:260px;font-size:22px;font-weight:700}
.result .role{position:absolute;top:460px;width:260px;font-size:14px;font-weight:700}
.result .stat{position:absolute;top:492px;width:260px;font-size:13px}

/* package */
.package{top:2671px;height:526px;overflow:hidden}
.package .disc{position:absolute;left:-120px;top:59px;width:408px;height:408px;border-radius:50%;background:var(--cyan)}
.package .pack{position:absolute;left:0;top:120px;width:330px;height:250px;background:linear-gradient(135deg,#f2f2f2,#e6b9cf 50%,#4d4d4d);transform:rotate(-8deg)}
.package .intro-q{position:absolute;left:398px;top:64px;font-size:20px;font-weight:700}
.package h3{position:absolute;left:398px;font-weight:400;color:var(--blue)}
.tick{position:absolute;left:398px;width:700px;padding-left:30px;font-size:13px;color:var(--body)}
.tick svg{position:absolute;left:0;top:2px}
.package .btn{left:398px;top:378px;width:116px;height:43px}

/* footer */
footer{top:3197px;height:396px;background:var(--footer);color:#ddd}
.f-brand{position:absolute;left:96px;top:110px;display:flex;align-items:center;gap:10px}
.f-brand .brand-dot{background:var(--white)}
.f-brand .brand-name{color:var(--white)}
.f-col h5{font-size:15px;font-weight:700;color:var(--white);letter-spacing:.5px}
.f-col{position:absolute;top:50px}
.links{list-style:none;margin-top:20px;font-size:14px;line-height:31px}
.contact-row{position:relative;padding-left:56px;margin-top:22px;font-size:13px;line-height:1.5}
.contact-row .ico{position:absolute;left:0;top:0;width:40px;height:40px;border-radius:50%;border:2px solid #bbb}
.contact-row b{color:var(--white);font-size:14px}
.cf-field{position:absolute;height:38px;border:1px solid #888;border-radius:2px;font-size:12px;color:#ddd;padding:11px 8px}
.cf-send{position:absolute;left:0;top:216px;width:118px;height:34px;background:var(--blue);color:var(--white);font-size:12px;font-weight:700;display:flex;align-items:center;justify-content:center}
.f-bottom{position:absolute;left:0;top:326px;width:1200px;border-top:1px solid #3a3a3a}
.copyright{position:absolute;left:96px;top:356px;font-size:13px}
.social{position:absolute;left:953px;top:344px;display:flex;gap:8px}
.social i{width:32px;height:32px;border-radius:50%;border:2px solid #ccc;display:block}
</style>
</head>
<body>

<header class="hero">
  <div class="hero-photo" role="img" aria-label="Photo of a smiling mum kneeling on a mat with a dumbbell while her baby reaches for it"></div>
  <div class="brand"><div class="brand-dot"></div><div class="brand-name">Tidewell Mamas<br><span style="font-size:13px;font-weight:400;color:var(--ink)">Home Fitness</span></div></div>
  <nav class="nav">
    <span style="left:383px">Home</span><span style="left:462px">About Us</span><span style="left:584px">Program</span><span style="left:706px">Blog</span><span style="left:797px">Shop</span><span style="left:886px">Contact Us</span>
  </nav>
  <div class="btn join">JOIN WITH US!</div>
  <h1>LOSE YOUR BABY WEIGHT</h1>
  <div class="script">Bounce Back into shape!</div>
  <div class="sub">12 week Home Workout Program For Mums!</div>
  <div class="btn">Get Started Now!</div>
  <div class="dots"><i></i><i></i><i></i><i></i><i></i></div>
</header>

<section class="intro">
  <h2>TIDEWELL MAMAS</h2>
  <div class="rule"></div>
  <div class="lead">Check out some of the awesome results already achieved by mums on our program</div>
  <div class="copy">
    <p>After a life time of competitive sports and as a qualified personal trainer, I thought I knew exactly what it would take to get my body back after having babies. I put on a massive 30 kgs with my first pregnancy and found myself in a situation for the first time in my life where I had to lose a lot of weight. You can imagine how frustrated I was to find that it took me 8 months to get even close to my pre-baby body, training and eating the same way I always had. I particularly struggled with my baby belly, that just wouldn't go away.</p>
    <p>This sparked a huge determination and curiosity within me and I spent the next 2 years studying and researching the body and training techniques for mums post pregnancy.</p>
  </div>
  <div class="btn">Read More</div>
  <div class="optin">
    <h3>GET YOUR FREE TOP 10 BABY BELLY BLASTING TIPS</h3>
    <div class="note">See our secret tips to a flatter yummy mummy tummy that you can start implementing for free today!</div>
    <div class="field">Name</div>
    <div class="field">Email</div>
    <div class="submit">GET IT FREE NOW!</div>
  </div>
  <div class="badge">For Free<br>Today!</div>
</section>

<section class="band">
  <div class="band-title" style="top:52px"><div class="pre">Join all the other mums achieving amazing results and</div><div class="main">BOUNCE BACK INTO THE BODY THAT YOU DESERVE!</div></div>
  <div class="card" style="left:100px"><div class="photo" role="img" aria-label="Photo of a mum holding her two young children" style="background:linear-gradient(135deg,#c79a84,#8a6a5c)"></div><div class="icon"></div><h4>Our unique 3 stage, 12 week training program</h4><p>Gradually build back your fitness and core strength and also lose baby weight with our training circuit and fitness program</p></div>
  <div class="card" style="left:445px"><div class="photo" role="img" aria-label="Photo of a mum exercising on a mat in her living room" style="background:linear-gradient(135deg,#6b5b57,#8c7aa8)"></div><div class="icon"></div><h4>Our unique 3 stage, 12 week training program</h4><p>Gradually build back your fitness and core strength and also lose baby weight with our training circuit and fitness program</p></div>
  <div class="card" style="left:790px"><div class="photo" role="img" aria-label="Photo of a mum doing a lunge workout at home" style="background:linear-gradient(135deg,#3a3a3a,#b0373f)"></div><div class="icon"></div><h4>Our unique 3 stage, 12 week training program</h4><p>Gradually build back your fitness and core strength and also lose baby weight with our training circuit and fitness program</p></div>
</section>

<section class="founder">
  <div class="photo" role="img" aria-label="Photo of the founder standing in a green workout top"></div>
  <div class="label">About Tidewell Mamas Founder</div>
  <div class="name">MARLA QUENNET</div>
  <div class="copy">
    <p>After a life time of competitive sports and as a qualified personal trainer, I thought I knew exactly what it would take to get my body back after having babies. I put on a massive 30 kgs with my first pregnancy and found myself in a situation for the first time in my life where I had to lose a lot of weight. You can imagine how frustrated I was to find that it took me 8 months to get even close to my pre-baby body, training and eating the same way I always had. I particularly struggled with my baby belly, that just wouldn't go away no matter how many crunches I crunched!</p>
    <p>This is how I came to create the <b>12 Week Home Workout Program For Mums</b>. I put pen to paper and wrote down all the training routines I used to get my body back after my second baby. I then tested it out on other mums to make sure it worked for others too and all of the mums I tested on lost at least 18cms across their body doing the program.</p>
  </div>
  <div class="btn">Read More</div>
</section>

<section class="results">
  <div class="band-title" style="top:50px"><div class="pre">Join all the other mums achieving amazing results and</div><div class="main" style="font-size:25px">OUR MUMS BEFORE AFTER PHOTOS</div></div>
  <svg class="abs" style="left:0;top:250px" width="1200" height="80" viewBox="0 0 1200 80"><path d="M0 40 C200 -10 350 90 600 40 S1000 -10 1200 40" fill="none" stroke="#fff" stroke-width="2" stroke-dasharray="8 6" opacity=".7"/></svg>
  <div class="result" style="left:74px"><div class="ring" style="background:var(--gold)"><div class="shot" role="img" aria-label="Before and after photos of Marla"></div></div><div class="who">Marla</div><div class="role">Tidewell Mamas Founder</div><div class="stat">Lost 12 kgs and 25 cms in 12 weeks!</div></div>
  <div class="result" style="left:325px"><div class="ring" style="background:var(--blue)"><div class="shot" role="img" aria-label="Before and after photos of Jessa"></div></div><div class="who">Jessa</div><div class="role">Olympic Games Gold Medalist</div><div class="stat">Lost 20 cms in 12 weeks!</div></div>
  <div class="result" style="left:605px"><div class="ring" style="background:var(--gold)"><div class="shot" role="img" aria-label="Before and after photos of Kit"></div></div><div class="who">Kit</div><div class="role">Tidewell Mama</div><div class="stat">Lost 18cms in 8 weeks!</div></div>
  <div class="result" style="left:876px"><div class="ring" style="background:var(--blue)"><div class="shot" role="img" aria-label="Before and after photos of Bree"></div></div><div class="who">Bree</div><div class="role">Tidewell Mama</div><div class="stat">Lost 31 cms and 10kgs in 8 weeks!</div></div>
</section>

<section class="package">
  <div class="disc"></div>
  <div class="pack" role="img" aria-label="Program equipment pack with DVD, workout cards and resistance bands"></div>
  <div class="intro-q">What's included in the program?</div>
  <h3 style="top:102px;font-size:24px">12 WEEK HOME WORKOUT PROGRAM - EQUIPMENT PACK</h3>
  <h3 style="top:148px;font-size:19px;font-weight:700">Our unique 3 stage, 12 week training program</h3>
  <div class="tick" style="top:182px"><svg width="20" height="16" viewBox="0 0 20 16"><path d="M2 8l6 6L18 2" fill="none" stroke="var(--blue)" stroke-width="3"/></svg>Gradually build back your fitness and core strength and also lose baby weight with our training circuit and fitness program. We take you through 6 workout programs that increase with intensity and are designed for new mums as well as experienced mums.</div>
  <h3 style="top:278px;font-size:19px;font-weight:700">Full Instructional Workout DVD and program cards for each program</h3>
  <div class="tick" style="top:314px"><svg width="20" height="16" viewBox="0 0 20 16"><path d="M2 8l6 6L18 2" fill="none" stroke="var(--blue)" stroke-width="3"/></svg>You can either do your home workout along with us on DVD, or use your program cards and do it yourself while hanging with your family watching your favourite tv shows.</div>
  <div class="btn">Read More</div>
</section>

<footer>
  <div class="f-brand"><div class="brand-dot"></div><div class="brand-name">Tidewell Mamas<br><span style="font-size:13px;font-weight:400;color:#ddd">Home Fitness</span></div></div>
  <div class="f-col" style="left:359px"><h5>QUICK LINKS</h5>
    <ul class="links"><li>› Home</li><li>› About Us</li><li>› Programs</li><li>› Blog</li><li>› Shop</li><li>› Contact</li></ul></div>
  <div class="f-col" style="left:558px;width:230px"><h5>CONTACT US</h5>
    <div class="contact-row"><span class="ico"></span><b>ADDRESS,</b><br>Larchmere Road, Denholt, 123, Ireland.</div>
    <div class="contact-row"><span class="ico"></span><b>PHONE:</b><br>180.047.3918</div>
    <div class="contact-row"><span class="ico"></span><b>Mail:</b><br>info@tidewellmamas.in</div></div>
  <div class="f-col" style="left:831px;width:271px;height:260px"><h5>CONTACT FORM</h5>
    <div class="cf-field" style="left:0;top:46px;width:128px">Name</div>
    <div class="cf-field" style="left:136px;top:46px;width:135px">Phone</div>
    <div class="cf-field" style="left:0;top:94px;width:271px;height:106px">Message</div>
    <div class="cf-send">SEND MESSAGE</div></div>
  <div class="f-bottom"></div>
  <div class="copyright">Copyright © 2016 Tidewell Mamas. All Right Reserved</div>
  <div class="social"><i></i><i></i><i></i><i></i></div>
</footer>

</body>
</html>
```